BRIGHTHOLD PROPERTY MANAGEMENT INC. WEBSITE

Please make the website more family-friendly.

I want a website to help me build my property management business by adding listing properties and creating an online application. Im open to any other ideas.
I want a WordPress designer to code it.

Here is my current website. www.brighthold.biz

IDEA: I like the website design https://www.pelicanclimateservices.com/

Thank you

Tom

Number of Pages Required

5+ page

```html
<!DOCTYPE html>
<html lang="en">
<head>
<meta charset="utf-8">
<title>Brighthold Property Management</title>
<link href="https://fonts.googleapis.com/css2?family=Lora:wght@400;500;700&family=Poppins:wght@400;500;600&display=swap" rel="stylesheet">
<style>
:root{
  --red:#a50f14;
  --red-dark:#8c0c10;
  --ink:#222;
  --muted:#555;
  --pink:#f3e2e4;
  --grey-bg:#f1efef;
  --line:#d8d8d8;
  --black:#0d0d0d;
}
*{box-sizing:border-box;margin:0;padding:0}
html,body{width:1200px;height:5217px;overflow:hidden}
body{position:relative;background:#fff;font-family:"Lora",serif;color:var(--ink)}
.abs{position:absolute}
a{color:inherit;text-decoration:none}

/* header */
.site-header{position:absolute;left:0;top:0;width:1200px;height:160px;background:#fff}
.brand{left:130px;top:88px;width:150px;text-align:center;color:var(--red);font-size:22px;font-weight:500;letter-spacing:.5px}
.brand-mark{left:185px;top:30px;width:40px;height:40px;border:3px solid var(--red)}
.brand-sub{left:126px;top:114px;width:160px;text-align:center;font-size:7px;color:var(--ink);letter-spacing:.3px}
.phone-btn{left:650px;top:40px;height:30px;display:flex;align-items:center;gap:12px;font-size:18px}
.phone-btn .ic{width:30px;height:30px;background:var(--red);display:flex;align-items:center;justify-content:center}
.hdr-btn{top:36px;height:40px;display:flex;align-items:center;justify-content:center;font-size:16px}
.btn-outline{left:862px;width:95px;border:2px solid var(--red);color:var(--red)}
.btn-solid{left:973px;width:96px;background:var(--red);color:#fff}
.main-nav{left:381px;top:104px;display:flex;gap:30px;font-size:15px;color:#333}
.main-nav .active{color:var(--red);border-bottom:2px solid var(--red);padding-bottom:4px}

/* hero */
.hero{position:absolute;left:0;top:160px;width:1200px;height:600px;background:linear-gradient(100deg,#3c4a2a 0%,#7d6a52 28%,#b9a68e 55%,#5a3a2c 75%,#c9c0b4 100%)}
.hero-title{left:130px;top:105px;color:#fff;font-size:46px;font-weight:700;letter-spacing:1px;background:rgba(60,30,20,.55);padding:2px 14px}
.hero-offer{left:130px;top:185px;color:#fff;font-size:33px;font-weight:700;line-height:42px;text-shadow:0 2px 6px rgba(0,0,0,.6)}
.search{left:310px;top:375px;width:580px;height:56px;background:#fff;display:flex;align-items:center;justify-content:space-between;padding:0 22px 0 26px;font-size:12px}

/* calculator */
.calc{left:130px;top:650px;width:940px;height:418px;background:#fff;box-shadow:0 6px 24px rgba(0,0,0,.15);display:flex}
.calc-form{width:535px;padding:36px 52px}
.calc-form h2{font-size:30px;font-weight:400;margin-bottom:50px}
.calc-grid{display:grid;grid-template-columns:205px 205px;column-gap:16px;row-gap:22px}
.field label{display:block;font-size:12px;margin-bottom:10px}
.field .box{height:44px;border:1px solid #999;display:flex;align-items:center;justify-content:space-between;padding:0 16px;font-size:12px}
.calc-btn{margin-top:24px;height:48px;width:426px;background:var(--red);color:#fff;font-size:17px;display:flex;align-items:center;justify-content:center}
.calc-result{flex:1;background:var(--grey-bg);padding:30px 52px}
.res-row{display:flex;height:34px;align-items:center;padding:0 20px;font-size:13px;margin-bottom:10px}
.res-row:nth-child(even){background:var(--pink)}
.res-row span:first-child{width:150px}

/* headings */
.sec-title{font-size:30px;font-weight:400}
.rule{width:100px;height:2px;background:var(--red)}

/* listings */
.listings-title{left:0;width:1200px;top:1156px;text-align:center}
.listings-rule{left:550px;top:1220px}
.card{top:1272px;width:302px;height:504px;border:1px solid #e2e2e2;background:#fff}
.card .photo{height:224px;background:linear-gradient(180deg,#7fb1e0 0%,#b5cde2 45%,#b89a78 70%,#8f8470 100%)}
.card .body{padding:30px 30px 0}
.card h3{font-size:15px;font-weight:400;line-height:24px;height:52px}
.card .price{color:var(--red);font-size:22px;margin:6px 0 10px}
.card .addr{font-size:11px;margin-bottom:30px}
.stats{display:flex;font-size:11px;line-height:15px;margin-bottom:26px}
.stats div{padding-right:20px;margin-right:18px;border-right:1px solid #999}
.stats div:last-child{border:0}
.small-btn{display:inline-block;background:var(--red);color:#fff;font-size:13px;padding:6px 13px}

/* welcome */
.welcome-photo{left:0;top:1857px;width:584px;height:485px;background:linear-gradient(135deg,#3c4148,#8a8d90 45%,#d7d2cb 70%,#efece7)}
.welcome{left:584px;top:1857px;width:616px;height:485px;background:var(--grey-bg)}
.welcome h2{left:66px;top:62px}
.welcome .rule{left:66px;top:124px;width:122px}
.welcome p{left:66px;top:158px;width:370px;font-size:14px;line-height:24px}
.welcome .small-btn{left:66px;top:370px}

/* pm */
.pm{left:130px;top:2398px;width:430px}
.pm h2{font-size:29px;font-weight:400;line-height:42px;margin-bottom:42px}
.pm p{font-size:14px;line-height:24px;margin-bottom:22px}
.pm-photo{left:584px;top:2342px;width:616px;height:540px;background:linear-gradient(120deg,#231833,#4a2f5e 45%,#7a5a7a 70%,#2b2139)}
.pm-photo .cap{right:30px;top:120px;color:#fff;font-family:"Poppins",sans-serif;font-weight:600;font-size:34px;line-height:38px}

/* cities */
.cities{left:130px;top:2935px;width:960px;display:grid;grid-template-columns:212px 254px 236px 260px;font-size:12px;line-height:21px}
.cities li{list-style:none;padding-left:18px;position:relative}
.cities li::before{content:"";position:absolute;left:0;top:8px;border-left:5px solid var(--red);border-top:3px solid transparent;border-bottom:3px solid transparent}

/* services */
.services{left:0;top:3132px;width:1200px;height:592px;background:linear-gradient(180deg,#8b78b8 0%,#b890c4 30%,#9a8aa6 55%,#3b3f45 80%,#2a2a2c 100%)}
.svc{text-align:center;color:#fff;font-size:13px;line-height:21px;width:130px}
.svc .circ{width:92px;height:92px;border:2px solid #fff;border-radius:50%;margin:8px auto 0;display:flex;align-items:center;justify-content:center}
.svc .stem{width:2px;margin:0 auto;background:#fff}
.svc-title{left:0;width:1200px;top:352px;text-align:center;color:#fff;font-size:50px;text-shadow:0 2px 8px rgba(0,0,0,.5)}

/* rates */
.rates-title{left:114px;top:3834px}
.rates{left:114px;top:3930px;width:344px}
.rate{display:flex;height:40px;align-items:center;padding-left:18px;font-size:14px;margin-bottom:8px}
.rate:nth-child(even){background:var(--pink)}
.rate span:first-child{width:195px}
.rates-photo{left:462px;top:3780px;width:608px;height:430px;background:linear-gradient(135deg,#6b5e52,#a89c8e 40%,#f2f2f0 55%,#7d7166)}

/* contact */
.contact{left:0;top:4268px;width:1200px;height:575px;background:linear-gradient(90deg,#5da230 0%,#9ccc55 35%,#b9d88a 60%,#dde9d4 85%,#f1eee9 100%)}
.contact h2{left:688px;top:72px;font-size:38px}
.contact .rule{left:688px;top:138px;width:126px}
.input{left:688px;width:380px;height:42px;background:#fff;border-radius:6px;border:1px solid #ddd;font-size:12px;padding:14px 18px}
.submit{left:688px;top:452px;width:380px;height:60px;border-radius:6px;background:var(--red);color:#fff;font-size:22px;display:flex;align-items:center;justify-content:center}

/* footer */
.footer{left:0;top:4843px;width:1200px;height:374px;background:var(--black);color:#fff;font-family:"Poppins",sans-serif}
.f-brand{left:130px;top:190px;width:280px;text-align:center;font-family:"Lora",serif;color:var(--red);font-size:32px}
.f-brand-sub{left:130px;top:232px;width:280px;text-align:center;font-family:"Lora",serif;font-size:11px;letter-spacing:1px}
.f-head{font-size:13px;font-weight:600;top:56px}
.f-line{height:1px;background:#555;top:80px}
.f-item{display:flex;gap:12px;font-size:11px;line-height:15px;align-items:center}
.f-dot{width:20px;height:20px;border-radius:50%;background:#fff;flex:none}
.f-menu{left:750px;top:116px;font-size:11px;line-height:19.5px}
.f-bottom{left:130px;top:312px;width:940px;height:1px;background:#444}
.copy{left:0;width:1200px;top:340px;text-align:center;font-size:10px}
</style>
</head>
<body>

<header class="site-header">
  <div class="abs brand-mark" aria-hidden="true"></div>
  <div class="abs brand">BRIGHTHOLD</div>
  <div class="abs brand-sub">PROPERTY MANAGEMENT &amp; SERVICES</div>
  <div class="abs phone-btn">
    <span class="ic"><svg width="16" height="16" viewBox="0 0 24 24"><path fill="#fff" d="M6.6 10.8a15 15 0 0 0 6.6 6.6l2.2-2.2a1 1 0 0 1 1-.25 11 11 0 0 0 3.6.6 1 1 0 0 1 1 1V20a1 1 0 0 1-1 1A17 17 0 0 1 3 4a1 1 0 0 1 1-1h3.5a1 1 0 0 1 1 1 11 11 0 0 0 .6 3.6 1 1 0 0 1-.25 1z"/></svg></span>
    (916) 555-0148
  </div>
  <a class="abs hdr-btn btn-outline">Contact</a>
  <a class="abs hdr-btn btn-solid">Login</a>
  <nav class="abs main-nav">
    <a class="active">Home</a><a>Listings</a><a>Owners</a><a>Prospect Tenants</a><a>About</a><a>Community</a><a>Mortgage Info</a>
  </nav>
</header>

<section class="hero" role="img" aria-label="Family walking happily into a bright new home with a plant by the door">
  <div class="abs hero-title">CALL TODAY</div>
  <div class="abs hero-offer">GET 1 MONTH PROPERTY<br>MANAGEMENT FEE OFF.<br>$120 VALUE!!</div>
  <div class="abs search">
    <span>Enter Address, City, Zip, Neighbourhood or #MLS</span>
    <svg width="20" height="20" viewBox="0 0 24 24"><circle cx="10" cy="10" r="7" fill="none" stroke="#a50f14" stroke-width="2.5"/><path d="M15 15l6 6" stroke="#a50f14" stroke-width="2.5"/></svg>
  </div>
</section>

<section class="abs calc">
  <div class="calc-form">
    <h2>Mortgage Calculator</h2>
    <div class="calc-grid">
      <div class="field"><label>Loan amount</label><div class="box">$150000</div></div>
      <div class="field"><label>Loan length</label><div class="box">30 Years</div></div>
      <div class="field"><label>Annual interest</label><div class="box">3.7%</div></div>
      <div class="field"><label>Pay periodicity</label><div class="box">Annually <svg width="12" height="8"><path d="M0 0h12L6 7z" fill="#222"/></svg></div></div>
    </div>
    <div class="calc-btn">Calculate</div>
  </div>
  <div class="calc-result">
    <div class="res-row"><span>Loan amount:</span><span>$150,000.00</span></div>
    <div class="res-row"><span>Loan length:</span><span>30 years</span></div>
    <div class="res-row"><span>Annual interest:</span><span>3.70%</span></div>
    <div class="res-row"><span>Pay periodicity:</span><span>Annually</span></div>
    <div class="res-row"><span>Annually payment:</span><span>$8,361.34</span></div>
    <div class="res-row"><span>Total paid:</span><span>$250,840.15</span></div>
    <div class="res-row"><span>Total interest:</span><span>$100,840.15</span></div>
    <div class="res-row"><span>Total periods:</span><span>30</span></div>
  </div>
</section>

<h2 class="abs sec-title listings-title">Listings</h2>
<div class="abs rule listings-rule"></div>

<article class="abs card" style="left:130px">
  <div class="photo" role="img" aria-label="Single-storey rental home with a large tree under blue sky"></div>
  <div class="body">
    <h3>Fantastic opportunity<br>2 Bdrm x 1 Bth ADU Unit!!</h3>
    <div class="price">$2,000.00</div>
    <div class="addr">1840 Linden St, Oakland, CA 94621</div>
    <div class="stats"><div>693<br>Sq. Ft</div><div>2<br>Bedrooms</div><div>1<br>Bathrooms</div></div>
    <span class="small-btn">View Details</span>
  </div>
</article>
<article class="abs card" style="left:450px">
  <div class="photo" role="img" aria-label="Apartment building front with shaded entrance"></div>
  <div class="body">
    <h3>4210 Maple Crest Ave #3</h3>
    <div class="price">$2,000.00</div>
    <div class="addr">Carmichael, CA 95608, Sacramento, US</div>
    <div class="stats"><div>693<br>Sq. Ft</div><div>2<br>Bedrooms</div><div>1<br>Bathrooms</div></div>
    <span class="small-btn">View Details</span>
  </div>
</article>
<article class="abs card" style="left:768px">
  <div class="photo" role="img" aria-label="Stucco apartment with tree and lawn"></div>
  <div class="body">
    <h3>Nice &amp; Clean 3 bd. x 1 bth.<br>Apartment.</h3>
    <div class="price">$1695.00</div>
    <div class="addr">Sacramento, CA 95818, Sacramento, US</div>
    <div class="stats"><div>693<br>Sq. Ft</div><div>2<br>Bedrooms</div><div>1<br>Bathrooms</div></div>
    <span class="small-btn">View Details</span>
  </div>
</article>

<div class="abs welcome-photo" role="img" aria-label="Hands holding a tablet over house plans beside a small model house"></div>
<section class="abs welcome">
  <h2 class="abs sec-title">Welcome to Brighthold</h2>
  <div class="abs rule"></div>
  <p class="abs">Our vision for Brighthold Property Management is to provide the best Property Management Services to the Sacramento and surrounding areas. I am focused on providing a more personalized service to you and your tenants. This means we are a one-stop-shop. You only deal with me, no middle guy, so no time is wasted.</p>
  <span class="abs small-btn">Read More</span>
</section>

<section class="abs pm">
  <h2>Property Management Elk Grove, Sacramento &amp; Surrounding Areas</h2>
  <p>Having the right property manager means having an agent who is committed to helping you and making being a home provider hassle free. I believe clear communication, work ethic, time management, staying focused and knowledge goes a long way in my business.</p>
  <p>This commitment level has helped us build a remarkable track record of delivering results and maintaining a long lasting business partnership with our clients.</p>
  <span class="small-btn">Read More</span>
</section>
<div class="abs pm-photo" role="img" aria-label="Hand touching a glowing digital dashboard">
  <div class="abs cap">PROPERTY<br>MANAGEMENT</div>
</div>

<ul class="abs cities">
  <div><li>Sacramento</li><li>Antelope</li><li>Carmichael</li><li>Citrus Heights</li><li>El Dorado County</li><li>El Dorado Hills</li></div>
  <div><li>Elverta</li><li>Fair Oaks</li><li>Folsom</li><li>Foothill Farms</li><li>Florin Vicinity</li><li>Land Park / Curtis Park</li></div>
  <div><li>Elk Grove / Laguna</li><li>Mather</li><li>Natomas</li><li>North Highlands</li><li>Orangevale</li><li>Galt</li></div>
  <div><li>Rancho Cordova / Gold River</li><li>Rancho Cordova / Anatolia &amp; Vicinity</li><li>Rancho Murieta</li><li>Rio Linda</li><li>Rocklin</li><li>Rosemont / Mayhew Vicinity</li></div>
</ul>

<section class="abs services" role="img" aria-label="Modern two-storey house with lit garage at dusk under a purple sky">
  <div class="abs svc" style="left:118px;top:88px">Rent<br>Collection<div class="circ"><svg width="40" height="40" viewBox="0 0 40 40" fill="none" stroke="#fff" stroke-width="2"><rect x="8" y="8" width="18" height="12"/><path d="M6 28h12l10-6"/></svg></div><div class="stem" style="height:28px"></div></div>
  <div class="abs svc" style="left:257px;top:66px">Mortgage &amp;<br>Utility Payments<div class="circ"><svg width="40" height="40" viewBox="0 0 40 40" fill="none" stroke="#fff" stroke-width="2"><path d="M6 20L20 8l14 12M10 18v14h20V18"/></svg></div><div class="stem" style="height:52px"></div></div>
  <div class="abs svc" style="left:402px;top:60px">Accounting<br>Services<div class="circ"><svg width="40" height="40" viewBox="0 0 40 40" fill="none" stroke="#fff" stroke-width="2"><rect x="10" y="6" width="20" height="28"/><path d="M14 14h12M14 20h12M14 26h8"/></svg></div><div class="stem" style="height:62px"></div></div>
  <div class="abs svc" style="left:535px;top:50px">Security<br>Deposits<div class="circ"><svg width="40" height="40" viewBox="0 0 40 40" fill="none" stroke="#fff" stroke-width="2"><rect x="8" y="8" width="24" height="24"/><circle cx="20" cy="20" r="6"/></svg></div><div class="stem" style="height:80px"></div></div>
  <div class="abs svc" style="left:670px;top:54px">Inspections<br>of Property<div class="circ"><svg width="40" height="40" viewBox="0 0 40 40" fill="none" stroke="#fff" stroke-width="2"><path d="M6 20L20 8l14 12M10 18v14h12"/><circle cx="27" cy="26" r="5"/><path d="M31 30l4 4"/></svg></div><div class="stem" style="height:70px"></div></div>
  <div class="abs svc" style="left:819px;top:54px">Repair &amp;<br>Maintenance<br>Service<div class="circ"><svg width="40" height="40" viewBox="0 0 40 40" fill="none" stroke="#fff" stroke-width="2"><path d="M8 32L30 10M10 10l22 22"/></svg></div><div class="stem" style="height:48px"></div></div>
  <div class="abs svc" style="left:958px;top:98px">Leasing<div class="circ"><svg width="40" height="40" viewBox="0 0 40 40" fill="none" stroke="#fff" stroke-width="2"><path d="M6 20L20 8l14 12M10 18v14h20V18"/><circle cx="20" cy="24" r="4"/></svg></div><div class="stem" style="height:40px"></div></div>
  <div class="abs svc-title">Property Management</div>
</section>

<h2 class="abs sec-title rates-title">Mortgage Rates</h2>
<div class="abs rates">
  <div class="rate"><span>30-Year FHA Rate</span><span>7.07%</span></div>
  <div class="rate"><span>30-Year Fixed Rate</span><span>5.88%</span></div>
  <div class="rate"><span>20-Year Fixed Rate</span><span>7.19%</span></div>
  <div class="rate"><span>15-Year Fixed Rate</span><span>6.61%</span></div>
</div>
<div class="abs rates-photo" role="img" aria-label="Tablet showing property management text on a wooden desk with coffee cup and pen"></div>

<section class="abs contact" role="img" aria-label="Yellow toy house with a red for-rent tag on green background">
  <h2 class="abs sec-title">Contact Us</h2>
  <div class="abs rule"></div>
  <div class="abs input" style="top:180px">First Name</div>
  <div class="abs input" style="top:234px">Last Name</div>
  <div class="abs input" style="top:288px">Email id</div>
  <div class="abs input" style="top:342px;height:96px">Message</div>
  <div class="abs submit">Submit</div>
</section>

<footer class="abs footer">
  <div class="abs f-brand">BRIGHTHOLD</div>
  <div class="abs f-brand-sub">PROPERTY MANAGEMENT &amp; SERVICES</div>

  <div class="abs f-head" style="left:462px">CONTACT US</div>
  <div class="abs f-line" style="left:462px;width:200px"></div>
  <div class="abs f-item" style="left:462px;top:122px"><span class="f-dot"></span><span>480 Larkfield Rd. #112<br>Sacramento , CA 95822</span></div>
  <div class="abs f-item" style="left:462px;top:178px"><span class="f-dot"></span><span>Call Us<br>(916) 555-0148</span></div>
  <div class="abs f-item" style="left:462px;top:232px"><span class="f-dot"></span><span>E-mail Us<br>info@brighthold.biz</span></div>

  <div class="abs f-head" style="left:750px">MENU</div>
  <div class="abs f-line" style="left:750px;width:106px"></div>
  <div class="abs f-menu">Home<br>Listings<br>Owners<br>Prospect Tenants<br>About<br>Community<br>Mortgage Info</div>

  <div class="abs f-head" style="left:962px">FOLLOW US</div>
  <div class="abs f-line" style="left:962px;width:106px"></div>
  <div class="abs f-item" style="left:962px;top:122px"><span class="f-dot"></span><span>Like us on<br>FRIENDPAGE</span></div>
  <div class="abs f-item" style="left:962px;top:172px"><span class="f-dot"></span><span>Follow us on<br>WORKLINK</span></div>
  <div class="abs f-item" style="left:962px;top:222px"><span class="f-dot"></span><span>Follow us on<br>PICSHARE</span></div>

  <div class="abs f-bottom"></div>
  <div class="abs copy">Copyright © 2024 All Rights Reserved</div>
</footer>

</body>
</html>
```